Professional Engineering Web Design

Project Brief: Website Redesign for Mechanical Design Consultancy
Project Overview
I want to update and improve my current website to create a more professional, modern, and high-credibility online presence for my mechanical design consultancy.

Current site: https://valtorix.design/

The new website must communicate expertise, precision, and trust—matching the standard of top engineering and product design agencies.

Reference Websites (Style + Structure Inspiration)
These represent the quality, cleanliness, and professionalism I want to achieve:

https://plinthwaredesign.com/
https://www.sorvane.com/
https://bramlow-uk.com/
Brand Look
Professional, modern, engineering-focused aesthetic
Clean layouts and strong typography
High-quality imagery conveying precision, innovation, and mechanical expertise
Colour scheme and styling must follow my existing logo (attached in project)
Platform Requirements
The website must be built on WordPress
Should use a clean, flexible theme or modern page builder (Elementor, Gutenberg, Bricks, or similar)
Avoid overly complex custom coding so I can easily edit content later
Final deliverable must allow me to manage and update content without developer assistance
Functionality
Fast-loading, lightweight, and smooth user experience
Clean animations and transitions similar to the reference sites
Fully mobile responsive
Clear navigation and strong visual hierarchy
Contact forms optimised for lead generation
Optional: subtle scroll effects, case study sliders, icon animations, etc.
SEO Aspirations
Developer should recommend and implement a modern SEO strategy
Proper on-page SEO setup (titles, meta, schema, alt tags, heading structure)
Optimised site architecture for ranking and crawling
Aim: Generate leads through improved visibility and keyword targeting
Optional but useful: Google Analytics, Google Search Console setup
User Journeys
(Recommended structure)

The site should be crafted around clear, intuitive journeys for each type of visitor:

Potential new clients
Quickly understand what services I offer
View examples of past work / case studies
See credibility indicators (process, expertise, industries served)
Easily contact me or request a project discussion
Returning clients
Access updated portfolio items
Find contact details or book follow-up work easily
General visitors discovering through SEO
Be guided to valtorix service areas
Understand my value proposition quickly
Be invited to learn more or make contact
The developer should design the structure to support these journeys smoothly.

Maintenance Expectations
Website will be maintained by me, so it should be easy to update using relatively basic WordPress skills
Use modular templates and simple backend structure
Avoid unnecessary plugins
Provide brief handover documentation if required
Hosting Preferences
Site is currently hosted via a family member
Open to discussing moving to a paid, reliable hosting provider if preferable for performance and maintainability
Developer may advise on the best hosting setup for WordPress
Content
Most content can be taken from the existing website
Developer is welcome to suggest improvements to structure, layout, and imagery
Must remain easy for me to edit or add new content later (e.g., new projects)
Deliverables
Fully built WordPress website
Clean, professional, modern design inspired by the reference sites
Mobile-responsive across all devices
SEO-ready structure and optimisations
Transfer of website and admin rights
Any design assets, templates, or documentation used

```html
<!DOCTYPE html>
<html lang="en">
<head>
<meta charset="utf-8">
<title>Valtorix Mechanical Design</title>
<link href="https://fonts.googleapis.com/css2?family=Archivo:wght@800;900&family=Outfit:wght@300;400;500;600&display=swap" rel="stylesheet">
<style>
:root{
  --blue:#3462ef;
  --blue-dark:#2450d8;
  --ink:#2a2c33;
  --text:#55585f;
  --muted:#8a8d94;
  --tint:#e9eefc;
  --tint-2:#f2f5fd;
  --dark:#2b2b2e;
  --white:#ffffff;
}
*{margin:0;padding:0;box-sizing:border-box}
html,body{width:1200px;height:4605px;overflow:hidden}
body{font-family:"Outfit",sans-serif;color:var(--ink);background:var(--white);position:relative}
section,header,footer{position:absolute;left:0;width:1200px}
.abs{position:absolute}
.blue{color:var(--blue)}
.pill{position:absolute;display:flex;align-items:center;justify-content:center;border-radius:30px;font-size:13px;font-weight:500;color:#fff;background:var(--blue);box-shadow:0 0 0 3px #fff,0 0 0 5px var(--blue)}
.eyebrow{font-size:14px;color:var(--blue);font-weight:400}
.heading{font-size:32px;font-weight:500;color:var(--ink);letter-spacing:-.3px}
.center{left:0;width:1200px;text-align:center}
.rule{position:absolute;height:3px;width:44px;background:var(--blue);left:578px}

/* header */
.site-header{top:0;height:77px;background:#fff;border-bottom:1px solid #eee}
.brand{position:absolute;left:141px;top:12px;display:flex;align-items:center;gap:10px}
.brand-dot{width:54px;height:54px;border-radius:50%;background:var(--blue)}
.brand-name{font-size:30px;font-weight:500;color:var(--ink);letter-spacing:3px;line-height:1}
.brand-sub{font-size:8px;color:var(--blue);letter-spacing:1.4px;font-weight:500}
.nav{position:absolute;left:468px;top:30px;display:flex;gap:22px;font-size:12px;color:var(--muted)}
.nav .active{color:var(--ink);border-bottom:2px solid var(--blue);padding-bottom:6px}
.search{position:absolute;left:815px;top:22px;height:34px;border-left:1px solid #ddd;padding-left:24px;display:flex;align-items:center;gap:8px;font-size:12px;color:var(--muted)}
.contact-btn{position:absolute;left:932px;top:18px;width:126px;height:40px;border-radius:22px;background:var(--dark);color:#fff;font-size:12px;display:flex;align-items:center;padding-left:18px}
.contact-btn .ic{position:absolute;right:4px;top:4px;width:32px;height:32px;border-radius:50%;background:#fff;display:flex;align-items:center;justify-content:center}

/* hero */
.hero{top:77px;height:660px;overflow:hidden}
.hero-photo{position:absolute;inset:0;background:linear-gradient(100deg,#2a2d35 0%,#3a4150 40%,#4f5a6c 62%,#6e4a3a 85%,#8a5a44 100%)}
.hero-shade{position:absolute;inset:0;background:linear-gradient(90deg,rgba(20,22,28,.75) 0%,rgba(20,22,28,.2) 55%,rgba(0,0,0,0) 100%)}
.hero-frame{position:absolute;left:107px;top:87px;width:75px;height:195px;border:2px solid #fff;border-right:none;border-radius:18px 0 0 18px}
.hero-frame:after{content:"";position:absolute;left:0;top:-2px;width:75px;border-top:2px solid #fff}
.hero-title{position:absolute;left:141px;top:112px;font-family:"Archivo",sans-serif;font-weight:900;font-size:52px;line-height:72px;color:#fff;letter-spacing:.5px}
.hero-sub{position:absolute;left:141px;top:257px;font-size:16px;line-height:29px;color:#fff;width:440px}
.hero-btn{left:141px;top:384px;width:192px;height:44px;justify-content:flex-start;padding-left:26px;box-shadow:none}
.hero-btn .ic{position:absolute;right:6px;top:6px;width:32px;height:32px;border-radius:50%;background:#fff;display:flex;align-items:center;justify-content:center}
.hero-wave{position:absolute;left:0;bottom:0;width:1200px;height:200px}
.scroll-dot{position:absolute;left:570px;top:513px;width:60px;height:60px;border-radius:50%;background:#fff;box-shadow:0 4px 14px rgba(0,0,0,.12);display:flex;align-items:center;justify-content:center}

/* welcome */
.welcome{top:737px;height:573px}
.welcome .eyebrow{position:absolute;left:143px;top:88px}
.welcome .heading{position:absolute;left:141px;top:106px}
.welcome-copy{position:absolute;left:143px;top:166px;width:405px;font-size:12.5px;line-height:23px;color:var(--text)}
.welcome-copy p+p{margin-top:3px}
.welcome-btn{left:145px;top:402px;width:136px;height:38px;font-size:12px}
.photo-ring{position:absolute;border-radius:50%;border:12px solid #3c3d42;overflow:hidden}
.photo-fill{width:100%;height:100%}
.badge-circle{position:absolute;border-radius:50%;background:var(--blue);display:flex;align-items:center;justify-content:center;color:#fff;font-size:20px;font-weight:500;letter-spacing:1px;box-shadow:0 0 0 10px #fff}

/* band */
.band{top:1310px;height:149px;background:var(--blue);color:#fff;text-align:center}
.band h2{margin-top:27px;font-size:25px;font-weight:500}
.band p{margin-top:8px;font-size:14px;line-height:23px}
.band-notch{position:absolute;left:520px;bottom:-1px;width:160px;height:22px}

/* expertise */
.expertise{top:1459px;height:654px}
.card{position:absolute;top:190px;width:283px;height:340px}
.card-img{position:absolute;left:0;top:0;width:283px;height:243px;border-radius:4px}
.card-icon{position:absolute;right:0;top:180px;width:66px;height:63px;background:var(--blue);display:flex;align-items:center;justify-content:center}
.card-body{position:absolute;left:40px;top:187px;width:243px;height:150px;background:#fff;padding:24px 20px 0 32px}
.card-body h3{font-size:17px;font-weight:500;line-height:27px;color:var(--ink)}
.card-body p{margin-top:10px;font-size:11.5px;line-height:23px;color:var(--text)}

/* projects */
.projects{top:2113px;height:828px;background:var(--tint)}
.tile{position:absolute;border-radius:14px;background:#fff;padding:6px;box-shadow:0 0 0 1px #d8dce6}
.tile-fill{width:100%;height:100%;border-radius:10px}
.feature{background:#c9cedd}
.feature-inner{position:absolute;left:10px;top:10px;right:10px;bottom:10px;border-radius:6px;background:linear-gradient(180deg,#3f6df2,#2f5ae8);color:#fff;text-align:center}
.feature-inner h3{margin-top:118px;font-size:18px;font-weight:500}
.feature-inner p{margin-top:10px;font-size:14px;line-height:25px}
.feature-btn{position:absolute;left:62px;top:231px;width:136px;height:38px;border-radius:20px;background:#fff;color:var(--ink);font-size:12px;display:flex;align-items:center;justify-content:center;box-shadow:0 0 0 3px var(--blue),0 0 0 5px #fff}

/* about */
.about{top:2941px;height:617px}
.about .eyebrow{position:absolute;left:662px;top:158px}
.about .heading{position:absolute;left:661px;top:176px}
.about .rule{left:662px;top:222px}
.about-copy{position:absolute;left:662px;top:236px;width:400px;font-size:14px;line-height:28px;color:var(--text)}
.about-btn{left:665px;top:420px;width:172px;height:38px;font-size:12px}

/* reviews */
.reviews{top:3558px;height:572px;background:linear-gradient(180deg,var(--tint) 0%,var(--tint-2) 100%)}
.review{position:absolute;top:232px;height:176px;background:#fff;border-radius:4px;padding:36px 24px 0 24px;font-size:11.5px;line-height:23px;color:var(--text)}
.review.on{background:var(--blue);color:#fff}
.review:after{content:"";position:absolute;left:28px;bottom:-40px;border-left:0 solid transparent;border-right:44px solid transparent;border-top:40px solid #fff}
.review.on:after{border-top-color:var(--blue)}
.quote{position:absolute;top:-18px;left:-2px;font-family:"Archivo",sans-serif;font-weight:900;font-size:58px;line-height:60px;color:var(--blue)}
.reviewer{position:absolute;top:428px;font-size:15px;color:var(--ink)}
.reviewer small{display:block;font-size:11px;color:var(--text)}
.stars{display:flex;gap:3px;margin-top:6px}
.arrow{position:absolute;top:306px;width:32px;height:32px;border:1.5px solid var(--blue);border-radius:4px;display:flex;align-items:center;justify-content:center;background:#fff}

/* cta */
.cta{top:4130px;height:125px;background:var(--blue)}
.cta h2{position:absolute;left:206px;top:34px;font-size:42px;font-weight:500;color:#fff}
.cta-btn{position:absolute;left:790px;top:42px;width:140px;height:42px;border-radius:22px;background:#27418f;color:#fff;font-size:15px;display:flex;align-items:center;justify-content:center;box-shadow:0 0 0 2px var(--blue),0 0 0 4px #fff}

/* footer */
.site-footer{top:4255px;height:350px;background:#fff}
.foot-brand{position:absolute;left:143px;top:93px;text-align:center;width:110px}
.foot-brand .dot{width:56px;height:56px;border-radius:50%;background:var(--blue);margin:0 auto 6px}
.foot-brand .name{font-size:30px;letter-spacing:3px;line-height:1}
.foot-brand .sub{font-size:8px;color:var(--blue);letter-spacing:1.2px;font-weight:500}
.socials{position:absolute;left:143px;top:222px;display:flex;gap:10px}
.socials span{width:28px;height:28px;border-radius:50%;border:1.5px solid var(--blue)}
.foot-col{position:absolute;top:100px}
.foot-col h4{font-size:15px;font-weight:500;color:var(--ink)}
.foot-col .rule{position:static;display:block;width:40px;height:2px;margin:10px 0 14px}
.foot-col li{list-style:none;font-size:11.5px;line-height:26px;color:var(--text)}
.contact-row{display:flex;gap:10px;font-size:11px;line-height:15px;color:var(--text);margin-bottom:10px}
.contact-row .ic{flex:none;width:26px;height:26px;border-radius:50%;border:1.5px solid var(--ink);display:flex;align-items:center;justify-content:center}
.map{width:224px;height:109px;border-radius:4px}
.copyright{position:absolute;left:0;top:297px;width:1200px;border-top:1px solid #e4e6ec;text-align:center;padding-top:18px;font-size:11.5px;color:var(--text)}
</style>
</head>
<body>

<header class="site-header">
  <div class="brand">
    <div class="brand-dot"></div>
    <div>
      <div class="brand-name">valtorix</div>
      <div class="brand-sub">MECHANICAL DESIGN</div>
    </div>
  </div>
  <nav class="nav">
    <span class="active">Home</span><span>About Us</span><span>Services</span><span>Portfolio</span><span>Process</span>
  </nav>
  <div class="search">
    <svg width="16" height="16" viewBox="0 0 16 16" fill="none" stroke="#8a8d94" stroke-width="1.5"><circle cx="7" cy="7" r="5"/><path d="M11 11l4 4"/></svg>
    Search...
  </div>
  <div class="contact-btn">Contact Us
    <span class="ic"><svg width="16" height="16" viewBox="0 0 24 24" fill="#2b2b2e"><path d="M6.6 10.8a15 15 0 006.6 6.6l2.2-2.2c.3-.3.7-.4 1-.2 1.1.4 2.3.6 3.6.6.6 0 1 .4 1 1V20c0 .6-.4 1-1 1A17 17 0 013 4c0-.6.4-1 1-1h3.5c.6 0 1 .4 1 1 0 1.3.2 2.5.6 3.6.1.3 0 .7-.2 1z"/></svg></span>
  </div>
</header>

<section class="hero">
  <div class="hero-photo" role="img" aria-label="Engineer wearing headphones working on a CAD model of gears across two monitors"></div>
  <div class="hero-shade"></div>
  <div class="hero-frame"></div>
  <h1 class="hero-title">MECHANICAL<br>CAD DESIGN</h1>
  <p class="hero-sub">Transforming concepts into production-ready designs with expertise and innovation</p>
  <div class="pill hero-btn">Start Your Project
    <span class="ic"><svg width="16" height="16" viewBox="0 0 24 24" fill="#3462ef"><path d="M6.6 10.8a15 15 0 006.6 6.6l2.2-2.2c.3-.3.7-.4 1-.2 1.1.4 2.3.6 3.6.6.6 0 1 .4 1 1V20c0 .6-.4 1-1 1A17 17 0 013 4c0-.6.4-1 1-1h3.5c.6 0 1 .4 1 1 0 1.3.2 2.5.6 3.6.1.3 0 .7-.2 1z"/></svg></span>
  </div>
  <svg class="hero-wave" viewBox="0 0 1200 200" preserveAspectRatio="none">
    <path d="M0 120 C 260 40, 520 20, 760 70 C 960 112, 1100 150, 1200 160 L1200 200 L0 200 Z" fill="#fff"/>
    <path d="M760 70 C 960 112, 1100 150, 1200 160 L1200 172 C 1090 160, 950 122, 760 74 Z" fill="#3462ef"/>
  </svg>
  <div class="scroll-dot">
    <svg width="26" height="26" viewBox="0 0 26 26" fill="none" stroke="#3462ef" stroke-width="1.6"><circle cx="13" cy="13" r="11"/><path d="M13 7v11M9 14l4 4 4-4"/></svg>
  </div>
</section>

<section class="welcome">
  <div class="eyebrow">Welcome To</div>
  <h2 class="heading">Valtorix <span class="blue">Mechanical Design</span></h2>
  <div class="welcome-copy">
    <p>Welcome to Valtorix Mechanical Design. We are a UK based design consultancy offering a comprehensive mechanical and product design service from initial concepts through to full volume production.</p>
    <p>At Valtorix Mechanical Design, we are committed to delivering innovative, high-quality engineering solutions tailored to meet the needs of our clients. Specializing in the design, development, and optimization of mechanical systems, we combine years of industry expertise with cutting-edge technology to ensure efficiency and precision in every project we undertake.</p>
  </div>
  <div class="pill welcome-btn">Contact us Today</div>
  <div class="photo-ring" style="left:637px;top:56px;width:424px;height:424px">
    <div class="photo-fill" role="img" aria-label="Designers reviewing a mechanical part model on two computer screens" style="background:linear-gradient(160deg,#c9d3dc,#6f8090 55%,#3e4a56)"></div>
  </div>
  <div class="badge-circle" style="left:584px;top:300px;width:152px;height:152px">valtorix</div>
</section>

<section class="band">
  <h2>Need reliable, accurate mechanical CAD designs for your project?</h2>
  <p>Whether you're developing prototypes, manufacturing parts, or optimizing existing systems,<br>our expert designers are ready to bring your concepts to life with cutting-edge CAD tools.</p>
  <svg class="band-notch" viewBox="0 0 160 22"><path d="M0 22 C 40 22, 50 2, 80 2 C 110 2, 120 22, 160 22 Z" fill="#fff"/><path d="M74 6l6 5 6-5M74 11l6 5 6-5" fill="none" stroke="#3462ef" stroke-width="1.4"/></svg>
</section>

<section class="expertise">
  <div class="abs center eyebrow" style="top:97px">Solutions</div>
  <h2 class="abs center heading" style="top:116px">Our <span class="blue">Expertise</span></h2>
  <div class="rule" style="top:163px"></div>

  <div class="card" style="left:141px">
    <div class="card-img" role="img" aria-label="Engineer in a hard hat holding a tablet in a workshop" style="background:linear-gradient(150deg,#b9c2cc,#7c8794 60%,#4f5965)"></div>
    <div class="card-icon"><svg width="36" height="36" viewBox="0 0 36 36" fill="none" stroke="#fff" stroke-width="1.5"><rect x="8" y="18" width="14" height="12"/><circle cx="15" cy="11" r="5"/><circle cx="27" cy="9" r="3"/><path d="M15 16v2M24 11l-4 3"/></svg></div>
    <div class="card-body"><h3>Bespoke<br>Product Design</h3><p>Innovative design from concept through the full development life cycle</p></div>
  </div>
  <div class="card" style="left:460px">
    <div class="card-img" role="img" aria-label="Designer working on a 3D model of a mechanical part on a monitor" style="background:linear-gradient(150deg,#8c9aaa,#51606f 55%,#2f3945)"></div>
    <div class="card-icon"><svg width="36" height="36" viewBox="0 0 36 36" fill="none" stroke="#fff" stroke-width="1.5"><rect x="5" y="6" width="26" height="18" rx="1"/><path d="M14 30h8M18 24v6M13 16l5-5 5 5v4h-10z"/></svg></div>
    <div class="card-body"><h3>3D Modelling<br>and Drawings</h3><p>We create 3D CAD, 2D engineering drawings and photorealistic renders</p></div>
  </div>
  <div class="card" style="left:776px">
    <div class="card-img" role="img" aria-label="Smiling designer holding a prototype part and a mug beside a laptop" style="background:linear-gradient(150deg,#d6d3cd,#a8a49c 55%,#7a766f)"></div>
    <div class="card-icon"><svg width="36" height="36" viewBox="0 0 36 36" fill="none" stroke="#fff" stroke-width="1.5"><circle cx="18" cy="16" r="7"/><circle cx="18" cy="16" r="2.5"/><path d="M18 6v3M18 23v3M8 16h3M25 16h3M6 30h24"/></svg></div>
    <div class="card-body"><h3>Design for<br>Manufacture</h3><p>Creating designs optimised for prototype and production manufacture</p></div>
  </div>
</section>

<section class="projects">
  <div class="abs center eyebrow" style="top:108px">Our Work</div>
  <h2 class="abs center heading" style="top:126px">Recent <span class="blue">Projects</span></h2>
  <div class="rule" style="top:173px"></div>
  <div class="abs center" style="top:183px;font-size:12px;color:var(--text)">A small selection of our previous projects</div>

  <div class="tile feature" style="left:141px;top:226px;width:283px;height:429px">
    <div class="feature-inner">
      <h3>Electrical Switchgear</h3>
      <p>Modern engineering applied to<br>70 year old relics</p>
      <div class="feature-btn">View All Projects</div>
    </div>
  </div>
  <div class="tile" style="left:436px;top:226px;width:267px;height:204px">
    <div class="tile-fill" role="img" aria-label="Render of a polished alloy wheel" style="background:radial-gradient(circle at 50% 50%,#9a9a9a 0,#e3e3e3 45%,#cfcfcf 100%)"></div>
  </div>
  <div class="tile" style="left:722px;top:226px;width:336px;height:204px">
    <div class="tile-fill" role="img" aria-label="Render of an action camera mounted on a yellow threaded rod rig" style="background:linear-gradient(120deg,#f4f4f4,#dedede 60%,#cfcfcf)"></div>
  </div>
  <div class="tile" style="left:436px;top:448px;width:335px;height:207px">
    <div class="tile-fill" role="img" aria-label="Render of a simulator seat frame with a steering wheel" style="background:linear-gradient(120deg,#f5f5f5,#e0e0e0 60%,#d2d2d2)"></div>
  </div>
  <div class="tile" style="left:789px;top:448px;width:269px;height:207px">
    <div class="tile-fill" role="img" aria-label="Render of a dark engine block assembly" style="background:radial-gradient(circle at 50% 55%,#3a3c40 0,#8a8c90 55%,#cfd0d2 100%)"></div>
  </div>
  <div class="pill" style="left:531px;top:693px;width:136px;height:38px;font-size:12px">View All Projects</div>
</section>

<section class="about">
  <div class="photo-ring" style="left:139px;top:93px;width:422px;height:422px">
    <div class="photo-fill" role="img" aria-label="Portrait photo of the chief engineer" style="background:linear-gradient(160deg,#e9ecef,#cfd4da 55%,#9ea6b0)"></div>
  </div>
  <div class="badge-circle" style="left:464px;top:353px;width:152px;height:152px">valtorix</div>
  <div class="eyebrow">About Me</div>
  <h2 class="heading">Rowan <span class="blue">Hale</span></h2>
  <div class="rule"></div>
  <p class="about-copy">Rowan Hale is the Chief Engineer at Valtorix Mechanical Design. He has 11 years experience working as a mechanical design engineer in multiple industries including high performance automotive, consumer products, medical, industrial plus many more. He has worked in multiple roles across a wide range of products.</p>
  <div class="pill about-btn">Tell us about your ideas</div>
</section>

<section class="reviews">
  <div class="abs center eyebrow" style="top:107px">Our Reviews</div>
  <h2 class="abs center heading" style="top:126px">What Our <span class="blue">Clients Say</span></h2>
  <div class="rule" style="top:173px"></div>
  <div class="abs center" style="top:183px;font-size:12px;color:var(--text)">A small selection of our previous projects</div>

  <div class="arrow" style="left:97px"><svg width="12" height="12" viewBox="0 0 12 12" fill="none" stroke="#3462ef" stroke-width="1.6"><path d="M8 2L4 6l4 4"/></svg></div>
  <div class="arrow" style="left:1069px"><svg width="12" height="12" viewBox="0 0 12 12" fill="none" stroke="#3462ef" stroke-width="1.6"><path d="M4 2l4 4-4 4"/></svg></div>

  <div class="review" style="left:154px;width:275px">
    <span class="quote">&ldquo;&ldquo;</span>
    Rowan went above and beyond in all aspects of the job. He identified issues with the design that I had not foreseen, rebuilt the design from scratch to ensure no aspect was overlooked, and...
  </div>
  <div class="review on" style="left:456px;width:286px">
    <span class="quote" style="color:#3c3d42">&ldquo;&ldquo;</span>
    Rowan was an excellent teammate on my project. He leveraged his considerable knowledge to make valuable recommendations and guide the design process effectively. He was flexible with...
  </div>
  <div class="review" style="left:769px;width:289px">
    <span class="quote">&ldquo;&ldquo;</span>
    "Rowan's description of his abilities was accurate. He is very capable and responsive. He worked very quickly and efficiently, cheerfully incorporating suggestions and revisions within a short...
  </div>

  <div class="reviewer" style="left:229px">MARCUS<small>Manager</small>
    <div class="stars"><svg width="100" height="16" viewBox="0 0 100 16" fill="#f5a623"><g id="st"><path d="M8 1l2.2 4.6 5 .7-3.6 3.5.9 5L8 12.4 3.5 14.8l.9-5L.8 6.3l5-.7z"/></g><use href="#st" x="20"/><use href="#st" x="40"/><use href="#st" x="60"/><use href="#st" x="80"/></svg></div>
  </div>
  <div class="reviewer" style="left:543px">TESSA<small>Manager</small>
    <div class="stars"><svg width="100" height="16" viewBox="0 0 100 16" fill="#f5a623"><use href="#st"/><use href="#st" x="20"/><use href="#st" x="40"/><use href="#st" x="60"/><use href="#st" x="80"/></svg></div>
  </div>
  <div class="reviewer" style="left:857px">ELLIOT BRANDE<small>Client</small>
    <div class="stars"><svg width="100" height="16" viewBox="0 0 100 16" fill="#f5a623"><use href="#st"/><use href="#st" x="20"/><use href="#st" x="40"/><use href="#st" x="60"/><use href="#st" x="80"/></svg></div>
  </div>
</section>

<section class="cta">
  <h2>Curious what else we do?</h2>
  <div class="cta-btn">SEE HERE</div>
</section>

<footer class="site-footer">
  <div class="foot-brand">
    <div class="dot"></div>
    <div class="name">valtorix</div>
    <div class="sub">MECHANICAL DESIGN</div>
  </div>
  <div class="socials"><span></span><span></span><span></span></div>

  <div class="foot-col" style="left:367px">
    <h4>Quick <span class="blue">Links</span></h4>
    <span class="rule"></span>
    <ul><li>Home</li><li>About Us</li><li>Portfolio</li><li>Our Services</li><li>Contact Us</li></ul>
  </div>

  <div class="foot-col" style="left:560px">
    <h4>Contact Details</h4>
    <span class="rule"></span>
    <div class="contact-row"><span class="ic"><svg width="12" height="12" viewBox="0 0 12 12" fill="none" stroke="#2a2c33" stroke-width="1.2"><path d="M6 11S2 7 2 4.5a4 4 0 018 0C10 7 6 11 6 11z"/><circle cx="6" cy="4.5" r="1.3"/></svg></span><span>48, Foundry Court, Marrow Lane<br>South Wales, UK.</span></div>
    <div class="contact-row"><span class="ic"><svg width="12" height="12" viewBox="0 0 24 24" fill="#2a2c33"><path d="M6.6 10.8a15 15 0 006.6 6.6l2.2-2.2c.3-.3.7-.4 1-.2 1.1.4 2.3.6 3.6.6.6 0 1 .4 1 1V20c0 .6-.4 1-1 1A17 17 0 013 4c0-.6.4-1 1-1h3.5c.6 0 1 .4 1 1 0 1.3.2 2.5.6 3.6.1.3 0 .7-.2 1z"/></svg></span><span>Phone<br>+44 (0)7700 900 418</span></div>
    <div class="contact-row"><span class="ic"><svg width="12" height="12" viewBox="0 0 12 12" fill="none" stroke="#2a2c33" stroke-width="1.2"><rect x="1.5" y="3" width="9" height="6.5"/><path d="M1.5 3L6 7l4.5-4"/></svg></span><span>Email<br>info@valtorix.design</span></div>
  </div>

  <div class="foot-col" style="left:835px">
    <h4>Our Locations</h4>
    <span class="rule"></span>
    <div class="map" role="img" aria-label="Map showing the studio location in South Wales" style="background:linear-gradient(135deg,#dfe8d8 0%,#e8ecef 50%,#9fd0ef 100%)"></div>
  </div>

  <div class="copyright">&copy; 2026 Valtorix Mechanical Design. All Rights Reserved.</div>
</footer>

</body>
</html>
```